Business Card design for law firm = Brightvale Australia

We are seeking a new design for our business cards.
We are keeping our logo, which is attached.
We need space for
Name
Title
Address is , which is
Level 7
214 Marlowe Street
Sydney NSW 2047
Phone :
Mobile :
Fax :
Email :
DX :
website www.brightvale-example.com.au

Industry/Entity Type

Law Firm / Banking and Finance

Contact Information for Business Card

We are seeking a new design for our business cards. We are keeping our logo. We need space for Name Title Address is Level 7 214 Marlowe Street Sydney NSW 2047 Phone Mobile Fax Email DX website www.brightvale-example.com.au

Colors
0054AA
0677BA
7BADD7
CADEEF
E8F1F8

Requirements
Must have
• see our website for general feel www.brightvale-example.com.au

```html
<!DOCTYPE html>
<html lang="en">
<head>
<meta charset="utf-8">
<title>Brightvale Australia — Business Card</title>
<link rel="stylesheet" href="https://fonts.googleapis.com/css2?family=Mulish:wght@400;600&display=swap">
<style>
  :root {
    --backdrop: #ababab;
    --navy: #022f5a;
    --teal: #0699c2;
    --brand-blue: #1c5ca8;
    --paper: #ffffff;
    --ink: #454545;
  }
  html, body {
    margin: 0;
    padding: 0;
    width: 1200px;
    height: 1000px;
    overflow: hidden;
    background: var(--backdrop);
    font-family: "Mulish", sans-serif;
  }
  .canvas {
    position: relative;
    width: 1200px;
    height: 1000px;
  }
  .card {
    position: absolute;
    width: 515px;
    height: 297px;
  }
  .card--front {
    left: 341px;
    top: 146px;
    background: var(--navy);
  }
  .card--back {
    left: 342px;
    top: 519px;
    background: var(--paper);
  }
  .front-mark {
    position: absolute;
    left: 0;
    right: 0;
    top: 110px;
    display: flex;
    flex-direction: column;
    align-items: center;
    gap: 14px;
  }
  .front-mark__square {
    width: 54px;
    height: 54px;
    background: var(--teal);
  }
  .front-mark__name {
    color: var(--paper);
    font-size: 22px;
    font-weight: 400;
    letter-spacing: 0.5px;
  }
  .brand {
    position: absolute;
    left: 260px;
    top: 28px;
  }
  .brand__square {
    width: 43px;
    height: 43px;
    background: var(--teal);
  }
  .brand__name {
    margin-top: 8px;
    color: var(--brand-blue);
    font-size: 25px;
    font-weight: 400;
    line-height: 1;
  }
  .brand__tagline {
    margin-top: 8px;
    color: var(--teal);
    font-size: 9.5px;
    letter-spacing: 0.6px;
  }
  .person {
    position: absolute;
    left: 36px;
    top: 153px;
  }
  .person__name {
    margin: 0;
    color: var(--brand-blue);
    font-size: 17.5px;
    font-weight: 600;
    letter-spacing: 0.3px;
  }
  .person__title {
    margin: 3px 0 0 1px;
    color: var(--teal);
    font-size: 9.5px;
    font-weight: 600;
    letter-spacing: 0.5px;
  }
  .contact {
    position: absolute;
    left: 258px;
    top: 154px;
    color: var(--ink);
    font-size: 13.2px;
    line-height: 17px;
    font-style: normal;
    letter-spacing: 0.2px;
  }
  .contact p {
    margin: 0;
  }
  .contact__address {
    margin-bottom: 17px !important;
  }
</style>
</head>
<body>
  <main class="canvas">
    <section class="card card--front" aria-label="Card front">
      <div class="front-mark">
        <div class="front-mark__square"></div>
        <div class="front-mark__name">Brightvale</div>
      </div>
    </section>

    <section class="card card--back" aria-label="Card back">
      <div class="brand">
        <div class="brand__square"></div>
        <div class="brand__name">Brightvale</div>
        <div class="brand__tagline">strategic legal outsourcing</div>
      </div>

      <div class="person">
        <h1 class="person__name">HELENA MARSH</h1>
        <p class="person__title">CHIEF LEGAL OFFICER</p>
      </div>

      <address class="contact">
        <p class="contact__address">Level 7, 214 Marlowe Street,<br>Sydney NSW 2047, DX 318 Sydney</p>
        <p>02 9555 0142</p>
        <p>02 9555 0187</p>
        <p>enquiries@brightvale-example.com.au</p>
        <p>www.brightvale-example.com.au</p>
      </address>
    </section>
  </main>
</body>
</html>
```